RESIDENTIAL CONSTRUCTION

We are a company that specializes in building custom residential homes, the design should also emphasize that quality and service is our priority.

Industry/Entity Type

Construction Company

Contact Information for Business Card

Contact Person: Marcus Lindqvist
Company Address: 273 West Alder Ave San Jose , Ca 95380
Phone Number : 408-731-2946
Email Address: Stoneridgehomes517@mailvista.net

Font styles to use
Sans Serif

Colors
ec1f27

Requirements
Must have
• CSLB # 7362015
Nice to have
• needs to have same color as logo i uploaded, we will be printing these on a clear plastic card.

```html
<!DOCTYPE html>
<html lang="en">
<head>
<meta charset="utf-8">
<title>Stoneridge General Builders – Business Card</title>
<link rel="stylesheet" href="https://fonts.googleapis.com/css2?family=Oswald:wght@500&family=Arimo:wght@400&display=swap">
<style>
  :root {
    --page-bg: #d9d6d2;
    --card-bg-top: #f4f3f1;
    --card-bg-bottom: #e4e2df;
    --brand-red: #a3161e;
    --brand-red-deep: #7e0f15;
    --swoosh-grey: #8e8e8e;
    --swoosh-light: #c9c9c9;
    --ink: #262626;
    --icon-fg: #ffffff;
  }
  * { box-sizing: border-box; margin: 0; padding: 0; }
  html, body {
    width: 1200px; height: 970px; overflow: hidden;
    background: var(--page-bg);
  }
  .business-card {
    position: absolute;
    left: 80px; top: 188px;
    width: 1040px; height: 594px;
    background: linear-gradient(160deg, var(--card-bg-top), var(--card-bg-bottom));
    overflow: hidden;
    box-shadow: 0 10px 30px rgba(0,0,0,0.18);
  }
  .card-graphics { position: absolute; inset: 0; }
  .company-name {
    position: absolute;
    left: 485px; top: 112px;
    width: 500px;
    font-family: "Oswald", sans-serif;
    font-weight: 500;
    font-size: 58px;
    line-height: 1.05;
    letter-spacing: 1px;
    color: var(--brand-red);
    text-transform: uppercase;
    display: flex; align-items: center; gap: 18px;
  }
  .company-name .mark-square {
    width: 26px; height: 26px; flex: none;
    background: var(--brand-red);
  }
  .license-number {
    position: absolute;
    right: 55px; top: 248px;
    font-family: "Arimo", sans-serif;
    font-size: 22px;
    letter-spacing: 1px;
    color: var(--ink);
  }
  .contact-name {
    position: absolute;
    left: 57px; top: 304px;
    font-family: "Oswald", sans-serif;
    font-weight: 500;
    font-size: 40px;
    letter-spacing: -0.5px;
    color: var(--ink);
    text-transform: uppercase;
  }
  .contact-list {
    position: absolute;
    left: 55px; top: 390px;
    list-style: none;
    font-family: "Arimo", sans-serif;
    font-size: 27px;
    color: var(--ink);
  }
  .contact-list li {
    display: flex; align-items: center; gap: 9px;
    height: 38px;
  }
  .contact-icon { width: 32px; height: 32px; flex: none; }
</style>
</head>
<body>
  <main class="business-card">
    <svg class="card-graphics" width="1040" height="594" viewBox="0 0 1040 594" aria-hidden="true">
      <defs>
        <linearGradient id="redBand" x1="0" y1="0" x2="1" y2="0">
          <stop offset="0" stop-color="#b01b23"/>
          <stop offset="1" stop-color="#7e0f15"/>
        </linearGradient>
      </defs>
      <path class="corner-red" d="M0 0 H150 Q50 40 0 112 Z" fill="var(--brand-red)"/>
      <path class="corner-swoosh-light" d="M0 112 Q80 30 150 0 H420 Q170 30 0 132 Z" fill="var(--swoosh-light)" opacity="0.7"/>
      <path class="corner-swoosh" d="M0 200 Q170 60 430 0 H470 Q210 60 0 232 Z" fill="var(--swoosh-grey)"/>
      <path class="bottom-swoosh" d="M0 528 Q540 590 1040 395 V414 Q540 606 0 548 Z" fill="var(--swoosh-grey)"/>
      <path class="bottom-red" d="M0 548 Q540 606 1040 414 V594 H0 Z" fill="url(#redBand)"/>
      <path class="bottom-edge" d="M0 574 Q520 600 1040 560 V566 Q520 606 0 580 Z" fill="var(--swoosh-light)" opacity="0.5"/>
    </svg>

    <div class="company-name"><span class="mark-square"></span><span>Stoneridge General Builders</span></div>
    <p class="license-number">CSLB # 7362015</p>

    <h1 class="contact-name">Marcus Lindqvist</h1>

    <ul class="contact-list">
      <li>
        <svg class="contact-icon" viewBox="0 0 32 32" aria-hidden="true">
          <circle cx="16" cy="16" r="16" fill="var(--brand-red)"/>
          <path d="M11 8 l3 0 l1.5 4.5 l-2 1.5 q1.5 3.5 4.5 4.5 l1.5 -2 l4.5 1.5 l0 3 q-1 2 -3 2 q-7 -1 -11 -8 q-1.5 -3 -1 -5 q0.5 -2 2 -2 z" fill="var(--icon-fg)"/>
        </svg>
        <span>408-731-2946</span>
      </li>
      <li>
        <svg class="contact-icon" viewBox="0 0 32 32" aria-hidden="true">
          <circle cx="16" cy="16" r="16" fill="var(--brand-red)"/>
          <rect x="8" y="10.5" width="16" height="11" fill="var(--icon-fg)"/>
          <path d="M8 10.5 L16 17 L24 10.5" fill="none" stroke="var(--brand-red)" stroke-width="1.5"/>
        </svg>
        <span>Stoneridgehomes517@mailvista.net</span>
      </li>
      <li>
        <svg class="contact-icon" viewBox="0 0 32 32" aria-hidden="true">
          <circle cx="16" cy="16" r="16" fill="var(--brand-red)"/>
          <path d="M16 26 Q9 17 9 13.5 A7 7 0 0 1 23 13.5 Q23 17 16 26 Z" fill="var(--icon-fg)"/>
          <circle cx="16" cy="13.5" r="2.8" fill="var(--brand-red)"/>
        </svg>
        <span>273 West Alder Ave San Jose, Ca 95380</span>
      </li>
    </ul>
  </main>
</body>
</html>
```